Travel Agency Website - Simple General

Need a 7 page simple design that is pretty repetitive. Need to be able to load quickly that is SEO optimized. Trying to give ideas on what they can do, be personal as we are local, but at the same time come across as professional and get information easily with little burden.

- Landing Page
- Brimwell Vacations Page
- Family Trips
- Road Trips from Texas
- Other Destinations
- About Us Page
- Contact Us Page

Target Market(s)

Families

Coding

Coded - Design and coding required

Number of Pages Required

5+ page

Colors

Designer to choose colors to be used in the design.

Requirements
Must have
• Like it to flow easily with our logo. Use that for colors, etc.

```html
<!DOCTYPE html>
<html lang="en">
<head>
<meta charset="utf-8">
<title>Other Destinations Page – Meadowlark Journeys</title>
<link rel="stylesheet" href="https://fonts.googleapis.com/css2?family=Jost:wght@400;500;600;700&family=Figtree:wght@400;500;600&display=swap">
<style>
:root{
  --stage:#a3a3a3;
  --teal:#1d5862;
  --teal-dark:#174b54;
  --gold:#c49a4f;
  --gold-light:#d9b777;
  --ink:#2c4a50;
  --paper:#f3f4ee;
  --mint:#e6eeec;
  --line:#b7c4c4;
  --white:#ffffff;
}
*{box-sizing:border-box;margin:0;padding:0}
html,body{width:1200px;height:991px;overflow:hidden}
body{background:var(--stage);font-family:"Figtree",sans-serif;color:var(--ink);position:relative}
.board-title{position:absolute;top:34px;left:0;width:1200px;text-align:center;font-family:"Jost",sans-serif;font-weight:600;font-size:60px;letter-spacing:1px;color:var(--white);line-height:1}

.page{position:absolute;width:880px;transform-origin:0 0;transform:scale(.5714);overflow:hidden;
  background:linear-gradient(180deg,#eef3f2 0%,#e9efed 45%,var(--paper) 100%)}
.page--split{left:80px;top:162px;height:1302px}
.page--centered{left:618px;top:162px;height:1104px}
.abs{position:absolute}

.contact-bar{position:absolute;left:400px;top:0;width:409px;height:29px;background:var(--teal);border-radius:0 0 8px 8px;display:flex;align-items:center;justify-content:center;gap:16px;color:var(--white);font-size:10.5px}
.contact-bar span{display:flex;align-items:center;gap:6px}
.contact-bar svg{width:18px;height:18px}

.brand{position:absolute;left:62px;top:10px;width:138px;height:110px;display:flex;flex-direction:column;align-items:center;justify-content:center;gap:6px}
.brand-dot{width:14px;height:14px;border-radius:50%;background:var(--gold)}
.brand-name{font-family:"Figtree",sans-serif;font-weight:600;font-size:19px;color:var(--teal);text-align:center;line-height:1.1}

.main-nav{position:absolute;top:47px;left:230px;height:27px;display:flex;align-items:center;font-size:11px;color:var(--ink)}
.main-nav a{color:inherit;text-decoration:none;margin-right:16px}
.main-nav .home{width:12px;height:12px;margin-right:14px}
.main-nav .current{color:var(--teal);border-bottom:1px solid var(--gold);padding-bottom:6px;margin-top:12px;margin-right:24px}
.btn{display:flex;align-items:center;justify-content:center;gap:10px;background:var(--gold);color:var(--white);border-radius:20px;font-weight:600}
.btn-round{display:inline-flex;align-items:center;justify-content:center;border-radius:50%;background:var(--gold-light)}
.nav-cta{width:101px;height:27px;font-size:10.5px;font-weight:500}
.nav-cta .btn-round{width:17px;height:17px}

.hero-photo{position:absolute;left:400px;top:92px;width:480px;height:300px;
  background:radial-gradient(ellipse at 55% 55%,#b08a3c 0%,#8a6d2e 18%,rgba(116,131,92,.7) 34%,rgba(170,192,210,.4) 58%,rgba(238,243,242,0) 78%),
  linear-gradient(180deg,#c9d5e2 0%,#a9bccb 40%,#9db7bf 75%,#e8efee 100%);
  -webkit-mask:linear-gradient(90deg,transparent 0%,#000 30%);mask:linear-gradient(90deg,transparent 0%,#000 30%)}
.eyebrow{font-family:"Jost",sans-serif;font-size:16px;color:var(--teal);letter-spacing:.3px}
.headline{font-family:"Jost",sans-serif;font-weight:600;color:var(--teal);letter-spacing:.5px;line-height:1.08}
.lede{font-size:15px;line-height:1.3;color:var(--teal)}
.spark{color:var(--gold);font-size:12px;position:absolute}

.gallery{position:absolute;display:grid;grid-template-columns:repeat(4,178px);grid-template-rows:131px 132px;gap:7px}
.tile{border-radius:3px}
.tile--tall{grid-row:span 2}
.t-venice{background:linear-gradient(180deg,#e3875a 0%,#c96a5b 40%,#8a6a6e 70%,#5b6f7b 100%)}
.t-boat{background:linear-gradient(180deg,#5f7a6a 0%,#2d8c92 45%,#1f7d84 70%,#a6693a 100%)}
.t-beach{background:linear-gradient(135deg,#3f8f5c 0%,#9fd3cf 50%,#e7e6d9 100%)}
.t-santorini{background:linear-gradient(180deg,#4e8fd0 0%,#2762b1 45%,#dfe4ea 70%,#8a7f6d 100%)}
.t-hikers{background:linear-gradient(180deg,#b4bcc6 0%,#7d8a8e 50%,#6e7b62 100%)}
.t-coast{background:linear-gradient(160deg,#2aa5e8 0%,#d1806c 35%,#b89f82 60%,#1e8fc4 100%)}

.plan-card{position:absolute;width:735px;height:444px;border:1px solid #d8ddd8;border-radius:6px;background:rgba(246,247,242,.75)}
.plan-title{position:absolute;top:32px;left:0;width:100%;text-align:center;font-family:"Jost",sans-serif;font-weight:600;font-size:24px;color:var(--teal);letter-spacing:.5px}
.field-label{position:absolute;font-size:12.5px;font-weight:500;color:var(--teal)}
.field{position:absolute;height:42px;border:1px solid #9aa8aa;border-radius:2px;background:var(--white);display:flex;align-items:center;padding:0 17px;font-size:12px;color:var(--teal)}
.field--select{justify-content:space-between}
.field--date{padding:0 10px;gap:8px}
.field--notes{height:82px;align-items:flex-start;padding-top:12px}
.field svg{flex:none}
.plan-btn{position:absolute;width:185px;height:39px;font-size:15px}
.plan-btn .btn-round{width:24px;height:24px}

.site-footer{position:absolute;left:0;bottom:0;width:880px;background:var(--white);display:flex;align-items:center;font-size:9.5px;color:var(--ink)}
.site-footer p{position:absolute;left:0;width:852px;text-align:center}
.social{position:absolute;right:114px;display:flex;gap:6px}
.social i{width:16px;height:16px;border-radius:50%;background:var(--teal);display:block}
</style>
</head>
<body>

<h1 class="board-title">OTHER DESTINATIONS PAGE</h1>

<!-- Split hero layout -->
<section class="page page--split">
  <div class="hero-photo" role="img" aria-label="Alpine lake with a church on a wooded island below snowy mountains"></div>

  <div class="contact-bar">
    <span><svg viewBox="0 0 18 18"><circle cx="9" cy="9" r="9" fill="#fff"/><rect x="4.5" y="6" width="9" height="6.5" rx="1" fill="none" stroke="#1d5862" stroke-width="1.2"/><path d="M4.8 6.4 9 9.6l4.2-3.2" fill="none" stroke="#1d5862" stroke-width="1.2"/></svg>hello@meadowlarkjourneys.com</span>
    <span><svg viewBox="0 0 18 18"><circle cx="9" cy="9" r="9" fill="#fff"/><path d="M6.2 4.8l1.6-.2 1 2.4-1.1.9a6 6 0 0 0 2.5 2.5l.9-1.1 2.4 1-.2 1.6c-3.8.5-7.5-3.2-7.1-7.1z" fill="#1d5862"/></svg>Phone Number (555) 010 2244</span>
  </div>

  <div class="brand"><span class="brand-dot"></span><span class="brand-name">Meadowlark<br>Journeys</span></div>

  <nav class="main-nav">
    <svg class="home" viewBox="0 0 12 12"><path d="M6 1 1 5.5h1.5V11h2.5V8h2v3h2.5V5.5H11z" fill="#c49a4f"/></svg>
    <a>Brimwell Vacations</a><a>Family Trips</a><a>Texas Road Trips</a><a class="current">Other Destinations</a><a>About Us</a>
    <span class="btn nav-cta">Contact Us <span class="btn-round"><svg width="8" height="8" viewBox="0 0 8 8"><path d="M1.5 6.5l5-5M2.5 1.5h4v4" stroke="#fff" fill="none" stroke-width="1.1"/></svg></span></span>
  </nav>

  <p class="eyebrow abs" style="left:88px;top:168px">OTHER DESTINATIONS</p>
  <h2 class="headline abs" style="left:87px;top:192px;font-size:35px">EXPLORE UNIQUE<br>DESTINATIONS</h2>
  <span class="spark" style="left:369px;top:180px">✦</span>
  <p class="lede abs" style="left:88px;top:279px;width:320px">Discover beautiful destinations, hidden gems, scenic escapes, and unforgettable travel experiences tailored to your style.</p>

  <div class="gallery" style="left:87px;top:431px">
    <div class="tile t-venice" role="img" aria-label="Venice canal at sunset"></div>
    <div class="tile tile--tall t-boat" role="img" aria-label="Traveller sitting in a wooden boat among limestone cliffs"></div>
    <div class="tile t-beach" role="img" aria-label="Aerial view of a tropical beach and forest"></div>
    <div class="tile tile--tall t-coast" role="img" aria-label="Colourful cliffside village above the sea"></div>
    <div class="tile t-santorini" role="img" aria-label="Blue-domed white church on a Greek island"></div>
    <div class="tile t-hikers" role="img" aria-label="Two hikers resting on a mountain"></div>
  </div>

  <div class="plan-card" style="left:83px;top:748px">
    <h3 class="plan-title">PLAN YOUR JOURNEY</h3>
    <span class="spark" style="left:571px;top:20px">✦</span>
    <p class="field-label" style="left:42px;top:90px">What Type of Trip Are You Interested In?</p>
    <p class="field-label" style="left:379px;top:90px">What Kind of Trip Are You Looking For?</p>
    <div class="field field--select" style="left:42px;top:116px;width:324px">Select<svg width="12" height="8" viewBox="0 0 12 8"><path d="M1 1.5l5 5 5-5" stroke="#1d5862" stroke-width="1.6" fill="none"/></svg></div>
    <div class="field field--select" style="left:376px;top:114px;width:325px">Select<svg width="12" height="8" viewBox="0 0 12 8"><path d="M1 1.5l5 5 5-5" stroke="#1d5862" stroke-width="1.6" fill="none"/></svg></div>
    <p class="field-label" style="left:42px;top:176px">How Many People in Your Party?</p>
    <p class="field-label" style="left:383px;top:176px">When Would You Like To Go?</p>
    <div class="field" style="left:42px;top:200px;width:324px">05</div>
    <div class="field field--date" style="left:378px;top:200px;width:158px"><svg width="13" height="13" viewBox="0 0 13 13"><rect x="1" y="2" width="11" height="10" rx="1" fill="none" stroke="#98a3a4"/><path d="M1 5h11M4 1v2M9 1v2" stroke="#98a3a4"/></svg>Start Date</div>
    <div class="field field--date" style="left:543px;top:200px;width:158px"><svg width="13" height="13" viewBox="0 0 13 13"><rect x="1" y="2" width="11" height="10" rx="1" fill="none" stroke="#98a3a4"/><path d="M1 5h11M4 1v2M9 1v2" stroke="#98a3a4"/></svg>End Date</div>
    <p class="field-label" style="left:42px;top:253px">Any Additional Notes</p>
    <div class="field field--notes" style="left:42px;top:276px;width:659px">Type here</div>
    <div class="btn plan-btn" style="left:277px;top:372px">Start Planning <span class="btn-round"><svg width="10" height="10" viewBox="0 0 8 8"><path d="M1.5 6.5l5-5M2.5 1.5h4v4" stroke="#fff" fill="none" stroke-width="1.1"/></svg></span></div>
  </div>

  <footer class="site-footer" style="height:57px">
    <p>© 2026 Meadowlark Journeys. All Right Reserved</p>
    <div class="social"><i></i><i></i></div>
  </footer>
</section>

<!-- Centered hero layout -->
<section class="page page--centered">
  <div class="contact-bar" style="left:394px">
    <span><svg viewBox="0 0 18 18"><circle cx="9" cy="9" r="9" fill="#fff"/><rect x="4.5" y="6" width="9" height="6.5" rx="1" fill="none" stroke="#1d5862" stroke-width="1.2"/><path d="M4.8 6.4 9 9.6l4.2-3.2" fill="none" stroke="#1d5862" stroke-width="1.2"/></svg>hello@meadowlarkjourneys.com</span>
    <span><svg viewBox="0 0 18 18"><circle cx="9" cy="9" r="9" fill="#fff"/><path d="M6.2 4.8l1.6-.2 1 2.4-1.1.9a6 6 0 0 0 2.5 2.5l.9-1.1 2.4 1-.2 1.6c-3.8.5-7.5-3.2-7.1-7.1z" fill="#1d5862"/></svg>Phone Number (555) 010 2244</span>
  </div>

  <div class="brand" style="left:56px"><span class="brand-dot"></span><span class="brand-name">Meadowlark<br>Journeys</span></div>

  <nav class="main-nav" style="left:224px;top:46px">
    <svg class="home" viewBox="0 0 12 12"><path d="M6 1 1 5.5h1.5V11h2.5V8h2v3h2.5V5.5H11z" fill="#c49a4f"/></svg>
    <a>Brimwell Vacations</a><a>Family Trips</a><a>Texas Road Trips</a><a class="current">Other Destinations</a><a>About Us</a>
    <span class="btn nav-cta">Contact Us <span class="btn-round"><svg width="8" height="8" viewBox="0 0 8 8"><path d="M1.5 6.5l5-5M2.5 1.5h4v4" stroke="#fff" fill="none" stroke-width="1.1"/></svg></span></span>
  </nav>

  <p class="eyebrow abs" style="left:0;top:118px;width:872px;text-align:center">OTHER DESTINATIONS</p>
  <h2 class="headline abs" style="left:0;top:142px;width:872px;text-align:center;font-size:31px">EXPLORE UNIQUE DESTINATIONS</h2>
  <span class="spark" style="left:668px;top:132px">✦</span>
  <p class="lede abs" style="left:150px;top:193px;width:572px;text-align:center">Discover beautiful destinations, hidden gems, scenic escapes, and unforgettable travel experiences tailored to your style.</p>

  <div class="gallery" style="left:82px;top:266px">
    <div class="tile t-venice" role="img" aria-label="Venice canal at sunset"></div>
    <div class="tile tile--tall t-boat" role="img" aria-label="Traveller sitting in a wooden boat among limestone cliffs"></div>
    <div class="tile t-beach" role="img" aria-label="Aerial view of a tropical beach and forest"></div>
    <div class="tile tile--tall t-coast" role="img" aria-label="Colourful cliffside village above the sea"></div>
    <div class="tile t-santorini" role="img" aria-label="Blue-domed white church on a Greek island"></div>
    <div class="tile t-hikers" role="img" aria-label="Two hikers resting on a mountain"></div>
  </div>

  <div class="plan-card" style="left:78px;top:574px">
    <h3 class="plan-title">PLAN YOUR JOURNEY</h3>
    <span class="spark" style="left:571px;top:20px">✦</span>
    <p class="field-label" style="left:42px;top:90px">What Type of Trip Are You Interested In?</p>
    <p class="field-label" style="left:379px;top:90px">What Kind of Trip Are You Looking For?</p>
    <div class="field field--select" style="left:42px;top:116px;width:324px">Select<svg width="12" height="8" viewBox="0 0 12 8"><path d="M1 1.5l5 5 5-5" stroke="#1d5862" stroke-width="1.6" fill="none"/></svg></div>
    <div class="field field--select" style="left:376px;top:114px;width:325px">Select<svg width="12" height="8" viewBox="0 0 12 8"><path d="M1 1.5l5 5 5-5" stroke="#1d5862" stroke-width="1.6" fill="none"/></svg></div>
    <p class="field-label" style="left:42px;top:176px">How Many People in Your Party?</p>
    <p class="field-label" style="left:383px;top:176px">When Would You Like To Go?</p>
    <div class="field" style="left:42px;top:200px;width:324px">05</div>
    <div class="field field--date" style="left:378px;top:200px;width:158px"><svg width="13" height="13" viewBox="0 0 13 13"><rect x="1" y="2" width="11" height="10" rx="1" fill="none" stroke="#98a3a4"/><path d="M1 5h11M4 1v2M9 1v2" stroke="#98a3a4"/></svg>Start Date</div>
    <div class="field field--date" style="left:543px;top:200px;width:158px"><svg width="13" height="13" viewBox="0 0 13 13"><rect x="1" y="2" width="11" height="10" rx="1" fill="none" stroke="#98a3a4"/><path d="M1 5h11M4 1v2M9 1v2" stroke="#98a3a4"/></svg>End Date</div>
    <p class="field-label" style="left:42px;top:253px">Any Additional Notes</p>
    <div class="field field--notes" style="left:42px;top:276px;width:659px">Type here</div>
    <div class="btn plan-btn" style="left:277px;top:372px">Start Planning <span class="btn-round"><svg width="10" height="10" viewBox="0 0 8 8"><path d="M1.5 6.5l5-5M2.5 1.5h4v4" stroke="#fff" fill="none" stroke-width="1.1"/></svg></span></div>
  </div>

  <footer class="site-footer" style="height:49px">
    <p>© 2026 Meadowlark Journeys. All Right Reserved</p>
    <div class="social" style="right:114px"><i></i><i></i></div>
  </footer>
</section>

</body>
</html>
```